Ad design for magazines to promote our Cloud Computing Consulting Company Branding

We need an advertisement design to promote our brand online and on printed magazines (full page). We are a cloud consulting company (products & services on the Cloud) and would like to create an ad that conveys confidence in our services.
Some of the ideas we would want to project are:
First Spanish consulting company specialized in Cloud Computing Technology and Services
We help you incorporate into your business the best Cloud Computing Solutions on the market to improve efficiency, reduce costs and increase competitiveness
Experts in:
• Cloud infrastructure modernization
• Digital Transformation, productivity and collaboration
• Cloud data management
• Advanced analytics
• Cloud application development
• Location Strategy
We are Norvane Sky Ally Prime and have recently achieved a Task Renewal Mastery award
We are also partners of other leading technologies
We have a web page to be used as reference even though we are open to designs that differ from this style. www.brevoltaconsult.example
Target Market(s)
B2B Market Business to Business
Requirements
Must have
- Dimensions: 21x29.7 cm. (width by height) CMYK, 300 dpi, 3 millimeters of bleed and cut lines
Nice to have
- We would like an attractive image with not a lot of text (just about what is on the explanation), including the Ally Prime and Task Renewal badges.

```html
<!DOCTYPE html>
<html lang="en">
<head>
<meta charset="utf-8">
<title>Brevolta Consult – Magazine Ad</title>
<link rel="stylesheet" href="https://fonts.googleapis.com/css2?family=Montserrat:wght@300;400;500;600;700;800;900&display=swap">
<style>
  :root {
    --stage: #e9e9e9;
    --paper-top: #f4f4f4;
    --paper-bottom: #e4e4e4;
    --brand-red: #e32127;
    --brand-teal: #35c4c6;
    --ink: #2b2b2b;
    --muted: #777777;
    --ring: #cfeff0;
    --art-deep: #3b2f8c;
    --art-soft: #c9c3ef;
  }
  * { margin: 0; padding: 0; box-sizing: border-box; }
  html, body { width: 1200px; height: 2591px; overflow: hidden; background: var(--stage); }
  body { position: relative; font-family: "Montserrat", sans-serif; }

  .ad-page {
    position: absolute; left: 50px; top: 517px; width: 1100px; height: 1556px;
    background: linear-gradient(180deg, var(--paper-top) 0%, #fafafa 45%, var(--paper-bottom) 100%);
    box-shadow: 0 8px 30px rgba(0,0,0,0.18);
    overflow: hidden;
  }
  .headline { position: absolute; left: 78px; top: 62px; }
  .headline-lead {
    color: var(--brand-red); font-weight: 300; font-size: 58px; line-height: 73px; letter-spacing: 1px;
  }
  .headline-focus {
    color: var(--brand-teal); font-weight: 800; font-size: 51px; line-height: 61px; margin-top: 12px;
  }
  .intro {
    position: absolute; left: 78px; top: 388px; width: 520px;
    font-size: 28px; line-height: 33px; color: var(--ink); font-weight: 400;
  }
  .intro strong { color: var(--brand-red); font-weight: 700; display: block; }

  .hero-art {
    position: absolute; left: 560px; top: 384px; width: 540px; height: 640px;
    background: radial-gradient(ellipse at 55% 55%, var(--art-soft) 0%, rgba(201,195,239,0.35) 45%, rgba(255,255,255,0) 72%),
                linear-gradient(160deg, rgba(59,47,140,0.15), rgba(53,196,198,0.12));
    border-radius: 8px;
  }

  .expert-map { position: absolute; left: 0; top: 0; width: 1100px; height: 1556px; }

  .experts-tag {
    position: absolute; left: 238px; top: 607px; width: 166px; height: 44px;
    background: var(--brand-red); color: #fff; font-weight: 500; font-size: 23px;
    line-height: 44px; padding-left: 18px; border-radius: 0 22px 22px 0;
  }
  .service-label {
    position: absolute; color: var(--brand-red); font-weight: 500; font-size: 23px; line-height: 27px;
  }
  .service-label.side { text-align: left; }
  .service-label.below { text-align: center; width: 220px; }

  .badge {
    position: absolute; left: 85px; top: 1340px; width: 158px; height: 158px;
    border-radius: 50%; background: #ffffff; border: 2px solid #9a9a9a;
  }
  .brand-mark {
    position: absolute; left: 318px; top: 1402px; width: 58px; height: 58px; background: var(--brand-red);
  }
  .brand {
    position: absolute; left: 403px; top: 1393px; width: 300px;
  }
  .brand-name {
    color: var(--brand-red); font-weight: 700; font-size: 29px; letter-spacing: 2px; line-height: 31px;
  }
  .brand-tagline {
    margin-top: 4px; color: var(--muted); font-size: 11px; letter-spacing: 1.5px; font-weight: 500;
  }
  .web-band {
    position: absolute; left: 730px; top: 1405px; width: 370px; height: 45px;
    background: var(--brand-teal); color: var(--ink); font-weight: 600; font-size: 17px;
    line-height: 45px; padding-left: 16px; letter-spacing: 0.5px;
  }
</style>
</head>
<body>
  <main class="ad-page">
    <header class="headline">
      <h1 class="headline-lead">FIRST SPANISH CONSULTING<br>COMPANY SPECIALIZED IN</h1>
      <h2 class="headline-focus">CLOUD COMPUTING TECHNOLOGY<br>AND SERVICES</h2>
    </header>

    <p class="intro">We help you incorporate into your business the best Cloud Computing Solutions on the market to improve
      <strong>efficiency, reduce costs and increase competitiveness</strong></p>

    <div class="hero-art" role="img" aria-label="Isometric illustration of a businessman beside a large server tower with a login panel and cloud platform on a circuit board"></div>

    <svg class="expert-map" viewBox="0 0 1100 1556" aria-hidden="true">
      <g fill="none" stroke="var(--brand-teal)" stroke-width="3">
        <polyline points="238,629 133,629 133,1150 1014,1150"/>
      </g>
      <g fill="var(--brand-teal)">
        <circle cx="238" cy="629" r="5"/>
        <circle cx="133" cy="862" r="5"/>
        <circle cx="336" cy="1150" r="5"/>
        <circle cx="574" cy="1150" r="5"/>
        <circle cx="812" cy="1150" r="5"/>
        <circle cx="1014" cy="1150" r="5"/>
      </g>
      <g class="service-nodes">
        <g transform="translate(133,757)"><circle r="58" fill="var(--ring)"/><circle r="49" fill="#fff" stroke="var(--brand-red)" stroke-width="5"/></g>
        <g transform="translate(133,966)"><circle r="58" fill="var(--ring)"/><circle r="49" fill="#fff" stroke="var(--brand-red)" stroke-width="5"/></g>
        <g transform="translate(217,1150)"><circle r="58" fill="var(--ring)"/><circle r="49" fill="#fff" stroke="var(--brand-red)" stroke-width="5"/></g>
        <g transform="translate(455,1150)"><circle r="58" fill="var(--ring)"/><circle r="49" fill="#fff" stroke="var(--brand-red)" stroke-width="5"/></g>
        <g transform="translate(693,1150)"><circle r="58" fill="var(--ring)"/><circle r="49" fill="#fff" stroke="var(--brand-red)" stroke-width="5"/></g>
        <g transform="translate(932,1150)"><circle r="58" fill="var(--ring)"/><circle r="49" fill="#fff" stroke="var(--brand-red)" stroke-width="5"/></g>
      </g>
      <g fill="none" stroke="#555" stroke-width="2.5" stroke-linecap="round" stroke-linejoin="round">
        <path d="M113,757 a10,10 0 0 1 8,-15 a13,13 0 0 1 24,2 a9,9 0 0 1 2,13 z M133,757 v10 M120,767 h26 M120,767 v6 M146,767 v6"/>
        <rect x="115" y="953" width="36" height="24" rx="2"/><path d="M109,982 h48"/>
        <rect x="199" y="1136" width="36" height="24" rx="2"/><path d="M193,1165 h48 M217,1146 v-14"/>
        <circle cx="450" cy="1156" r="9"/><path d="M458,1138 l8,-8 M462,1146 h10"/>
        <rect x="681" y="1130" width="24" height="40" rx="4"/><path d="M687,1150 h12"/>
        <rect x="914" y="1132" width="36" height="26" rx="2"/><path d="M932,1158 v12 M920,1170 h24"/>
      </g>
    </svg>

    <div class="experts-tag">Experts in:</div>
    <p class="service-label side" style="left:231px; top:740px;">Cloud infrastructure<br>modernization</p>
    <p class="service-label side" style="left:231px; top:930px;">Digital Transformation,<br>productivity and<br>collaboration</p>
    <p class="service-label below" style="left:107px; top:1232px;">Cloud data<br>management</p>
    <p class="service-label below" style="left:345px; top:1232px;">Advanced<br>analytics</p>
    <p class="service-label below" style="left:583px; top:1232px;">Cloud application<br>development</p>
    <p class="service-label below" style="left:822px; top:1232px;">Location Strategy</p>

    <div class="badge" role="img" aria-label="Task Renewal Mastery award badge"></div>

    <span class="brand-mark" aria-hidden="true"></span>
    <div class="brand">
      <div class="brand-name">BREVOLTA<br>CONSULT</div>
      <div class="brand-tagline">THE CLOUD CONSULTING COMPANY</div>
    </div>

    <div class="web-band">www.brevoltaconsult.example</div>
  </main>
</body>
</html>
```